Web design for a honey company

We are a honey retailing company currently looking for creative design for 3 pages of our existing e-commerce website which can be found here www.alpha.tolvenmarsk.co.nz. The designs need to be responsive i.e. presented in both desktop and mobile versions. We want to use the existing page color pallet, however any fonts can be used. Please use the texts and graphic content in the attachment files provided. For more detailed instructions please. The page does not require coding, the output files should be provided as layered and editable PSD.<br/><br/>Task 2: design 2 home page banners. Images, texts and the concept provided in the "layout structure" file. <br/><br/>The web designs should be presented in both desktop and mobile versions. We are looking for professional designer submissions only!

Target Market(s)

Hi-end consumers
Health conscious consumers

Number of Pages Required

3 page

Requirements
Must have
• 50% of images supplied along + any suggested stock images.
• Supplied texts integrated in the designs.
• Please only use the product images we have provided!
Should not have
• Clipart vector bees, vector honey slots or combs.
• No images of honey in glass jars!
• Do not use images of the traditional honey wooden spoons!
• Do not use images of any other but Manuka flower!

```html
<!DOCTYPE html>
<html lang="en">
<head>
<meta charset="utf-8">
<title>Tolvenmarsk Honey – Home</title>
<link href="https://fonts.googleapis.com/css2?family=Noto+Serif:wght@400;700&display=swap" rel="stylesheet">
<style>
:root{
  --stage:#ececec;
  --ink:#1f2024;
  --gold:#c9a24e;
  --gold-soft:#d4ad5a;
  --cream:#fbf1dc;
  --white:#ffffff;
  --text:#3a3a3a;
}
*{margin:0;padding:0;box-sizing:border-box}
html,body{width:757px;height:1200px;overflow:hidden;background:var(--stage);font-family:"Noto Serif",serif}
h1,h2{font-weight:400}
.page{position:absolute;top:20px;width:354px;height:1154px;background:var(--white);overflow:hidden;box-shadow:0 0 3px rgba(0,0,0,.15)}
.page--home{left:21px}
.page--menu{left:384px}
.abs{position:absolute}
.center{left:0;right:0;text-align:center}

.header{top:0;left:0;width:354px;height:40px;background:var(--ink)}
.brand{left:33px;top:6px;width:54px;height:28px;display:flex;align-items:center;justify-content:center;gap:3px;color:var(--gold);font-size:6px;letter-spacing:.3px}
.brand-dot{width:5px;height:5px;border-radius:50%;background:var(--gold)}
.login{left:259px;top:6px;width:26px;height:12px;border-radius:6px;background:var(--gold);color:var(--white);font-size:4px;line-height:12px;text-align:center}
.cart{left:290px;top:8px;color:var(--gold);font-size:5px}
.nav{top:26px;left:159px;font-size:4px;color:var(--white);white-space:nowrap}
.nav span{position:absolute;top:0}
.nav .active{color:var(--gold)}

.hero{top:40px;left:0;width:354px;height:194px;background:radial-gradient(circle at 55% 45%,#a8621a 0%,#c98a2a 30%,#e0b23c 55%,#6b4a22 100%)}
.hero-title{left:38px;top:119px;color:var(--white);font-size:14px;font-weight:700}
.hero-sub{left:38px;top:137px;color:var(--white);font-size:13px}
.btn{border-radius:12px;background:var(--gold);color:var(--white);text-align:center}
.hero-btn{left:38px;top:161px;width:56px;height:19px;font-size:6px;line-height:19px}
.dots{display:flex;gap:2px;justify-content:center}
.dots i{display:block;width:3px;height:3px;border-radius:50%;background:var(--white)}
.dots i.on{background:#e7c77a}
.hero-dots{top:222px}

.title{font-size:11px;color:var(--ink)}
.orn{width:60px;height:10px;margin:0 auto;background:linear-gradient(90deg,transparent,var(--gold) 30%,var(--gold) 70%,transparent);opacity:.6;border-radius:5px}
.para{font-size:4px;color:var(--text);line-height:10px}

.welcome-title{top:260px}
.welcome-orn{top:280px}
.welcome-text{top:283px;left:60px;width:234px}
.learn{left:141px;top:352px;width:72px;height:19px;font-size:5px;line-height:19px}

.products{top:390px;left:0;width:354px;height:224px;background:var(--cream)}
.products .title{top:12px}
.products .orn{position:absolute;left:147px;top:29px}
.products .sub{top:43px}
.sub{font-size:4.5px;color:var(--text)}
.card{top:66px;width:90px;height:128px;background:rgba(255,255,255,.7)}
.card-img{left:18px;top:8px;width:54px;height:60px;border-radius:4px;background:linear-gradient(160deg,#2b2a28,#1a1a1a 60%,#3b6b52)}
.card-heart{top:72px;font-size:5px;color:var(--gold)}
.card-name{top:81px;font-size:5px;color:var(--ink)}
.card-price{top:91px;font-size:4px;color:var(--gold)}
.card-btn{left:27px;top:104px;width:36px;height:13px;border:1px solid var(--gold);border-radius:7px;font-size:4px;color:var(--gold);line-height:11px;text-align:center}
.products .dots{position:absolute;left:0;right:0;top:208px}
.products .dots i{background:var(--ink)}
.products .dots i.on{background:var(--gold)}

.video{top:614px;left:0;width:354px;height:149px;background:linear-gradient(120deg,#4b5445,#7d8a78 40%,#3c4a3e 70%,#2a2f2a)}
.video-title{top:48px;font-size:14px;color:var(--white)}
.video-sub{top:70px;font-size:5.5px;color:var(--white)}
.play{left:162px;top:81px;width:30px;height:30px}

.articles{top:763px;left:0;width:354px;height:188px}
.articles .title{top:14px}
.articles .orn{position:absolute;left:147px;top:31px}
.articles .sub{top:48px}
.post{top:65px;width:69px;height:105px;background:var(--white);border:1px solid #ececec}
.post-img{left:0;top:0;width:67px;height:61px}
.post-text{top:66px;left:2px;right:2px;font-size:4px;line-height:8px;color:var(--text)}
.post-meta{top:87px;left:0;right:0;border-top:1px solid #eee;padding-top:4px;font-size:4px;color:var(--gold);text-align:center}

.newsletter{top:951px;left:0;width:354px;height:95px;background:var(--gold-soft)}
.newsletter .title{top:12px;color:var(--white)}
.newsletter .sub{top:33px;color:var(--white)}
.email{left:63px;top:44px;width:228px;height:16px;background:var(--white);font-size:4.5px;color:var(--text);padding-left:7px;line-height:16px}
.submit{left:152px;top:66px;width:50px;height:15px;background:var(--ink);color:var(--white);font-size:4.5px;line-height:15px;text-align:center;border-radius:2px}

.footer{top:1046px;left:0;width:354px;height:108px;background:var(--ink)}
.footer-brand{left:0;right:0;top:14px;display:flex;justify-content:center;align-items:center;gap:4px;color:var(--gold);font-size:10px}
.footer-brand .brand-dot{width:8px;height:8px}
.footer-nav{top:58px;left:91px;font-size:4px;color:var(--white);white-space:nowrap}
.footer-nav span{position:absolute;top:0}
.footer-nav .active{color:var(--gold)}
.pay{top:72px;left:0;right:0;display:flex;justify-content:center;gap:5px}
.pay span{font-size:4.5px;color:var(--ink);background:var(--white);padding:2px 4px;border-radius:2px}
.copy{top:90px;font-size:4px;color:var(--white)}

.dropdown{left:178px;top:38px;width:143px;height:96px;background:var(--white);box-shadow:0 2px 6px rgba(0,0,0,.2)}
.dropdown ul{position:absolute;top:11px;list-style:none;font-size:4px;color:var(--text)}
.dropdown li{height:11px}
.dropdown li::before{content:"» ";color:var(--ink)}
</style>
</head>
<body>

<!-- Home page, default state -->
<div class="page page--home">
  <header class="abs header">
    <div class="abs brand"><span class="brand-dot"></span>TOLVENMARSK</div>
    <div class="abs login">LOGIN</div>
    <div class="abs cart">&#128722; 0 / $0.00</div>
    <nav class="abs nav">
      <span class="active" style="left:0">HOME</span><span style="left:27px">SHOP ▾</span><span style="left:53px">QUALITY</span><span style="left:80px">ABOUT TOLVENMARSK</span><span style="left:134px">CONTACT US</span>
    </nav>
  </header>
  <section class="abs hero" role="img" aria-label="Honey pouring into a glass bowl among yellow flowers with bees"></section>
  <h1 class="abs hero-title">The Purest</h1>
  <p class="abs hero-sub">Teste of New Zealand</p>
  <div class="abs btn hero-btn">Shop Now</div>
  <div class="abs center dots hero-dots"><i></i><i class="on"></i><i></i></div>

  <h2 class="abs center title welcome-title">Welcome To Tolvenmarsk Honey</h2>
  <div class="abs center welcome-orn" style="top:270px"><div class="orn" role="img" aria-label="Gold ornamental flourish"></div></div>
  <p class="abs center para welcome-text" style="top:287px">Sed ut perspiciatis unde omnis iste natus error sit voluptatem accusantium doloremque laudantium, totam rem aperiam, eaque ipsa quae ab illo inventore veritatis et quasi architecto beatae vitae dicta sunt explicabo. Nemo enim ipsam volupt atem quia voluptas sit aspernatur aut odit aut fugit, sed quia consequuntur magni dolores eos qui ratione voluptatem ipsum quia dolor sit amet, consectetur, adipisci velit, sed quia non numquam eius</p>
  <div class="abs btn learn">LEARN MORE</div>

  <section class="abs products">
    <h2 class="abs center title">Our Products</h2>
    <div class="orn" role="img" aria-label="Gold ornamental flourish"></div>
    <p class="abs center sub">Sed ut perspiciatis unde omnis iste natus error sit voluptatem accusantium doloremque</p>
    <article class="abs card" style="left:33px"><div class="abs card-img" role="img" aria-label="Two jars of manuka honey MGO 100"></div><div class="abs center card-heart">♡</div><div class="abs center card-name">Miele Di Manuka MG100+</div><div class="abs center card-price">USD $18.00 – USD $22.00</div><div class="abs card-btn">BUY NOW</div></article>
    <article class="abs card" style="left:132px"><div class="abs card-img" role="img" aria-label="Jar of manuka honey MGO 300"></div><div class="abs center card-heart">♡</div><div class="abs center card-name">MGO 300+ Manuka Honey</div><div class="abs center card-price">USD $25.00 – USD $35.00</div><div class="abs card-btn">BUY NOW</div></article>
    <article class="abs card" style="left:231px"><div class="abs card-img" role="img" aria-label="Jar of manuka honey MGO 400"></div><div class="abs center card-heart">♡</div><div class="abs center card-name">MGO 400+ Manuka Honey</div><div class="abs center card-price">USD $25.00 – USD $35.00</div><div class="abs card-btn">BUY NOW</div></article>
    <div class="dots"><i></i><i class="on"></i><i></i></div>
  </section>

  <section class="abs video" role="img" aria-label="Beekeepers in protective suits tending hives in a field">
    <h2 class="abs center video-title">HOW OUR HONEY IS MADE</h2>
    <p class="abs center video-sub">Sed ut perspiciatis unde omnis iste natus error sit</p>
    <svg class="abs play" viewBox="0 0 30 30"><circle cx="15" cy="15" r="14" fill="rgba(0,0,0,.35)" stroke="#fff" stroke-width="1.2"/><path d="M12 9 L21 15 L12 21Z" fill="#fff"/></svg>
  </section>

  <section class="abs articles">
    <h2 class="abs center title">Latest Article</h2>
    <div class="orn" role="img" aria-label="Gold ornamental flourish"></div>
    <p class="abs center sub">Sed ut perspiciatis unde omnis iste natus error sit voluptatem accusantium doloremque</p>
    <article class="abs post" style="left:33px"><div class="abs post-img" role="img" aria-label="Bee on a pink flower" style="background:linear-gradient(135deg,#4d8a2e,#c24fb0 50%,#3e6b22)"></div><p class="abs center post-text">Sed ut perspiciatis unde omnis iste natus error</p><div class="abs post-meta">◉ 2 days ago</div></article>
    <article class="abs post" style="left:106px"><div class="abs post-img" role="img" aria-label="Beekeeper holding a honeycomb frame" style="background:linear-gradient(135deg,#d9cdb0,#b88a3a 50%,#6e4a1f)"></div><p class="abs center post-text">Sed ut perspiciatis unde omnis iste natus error</p><div class="abs post-meta">◉ 2 days ago</div></article>
    <article class="abs post" style="left:180px"><div class="abs post-img" role="img" aria-label="Bees on golden honeycomb" style="background:linear-gradient(135deg,#f0b426,#d98a10 50%,#8a5208)"></div><p class="abs center post-text">Sed ut perspiciatis unde omnis iste natus error</p><div class="abs post-meta">◉ 2 days ago</div></article>
    <article class="abs post" style="left:253px"><div class="abs post-img" role="img" aria-label="Honey in a glass bowl with yellow flowers" style="background:linear-gradient(135deg,#e8b830,#b5621a 50%,#6b3a12)"></div><p class="abs center post-text">Sed ut perspiciatis unde omnis iste natus error</p><div class="abs post-meta">◉ 2 days ago</div></article>
  </section>

  <section class="abs newsletter">
    <h2 class="abs center title">Our Newsletter</h2>
    <p class="abs center sub">Sed ut perspiciatis unde omnis iste natus error sit voluptatem accusantium doloremque</p>
    <div class="abs email">Email id :</div>
    <div class="abs submit">SUBMIT</div>
  </section>

  <footer class="abs footer">
    <div class="abs footer-brand"><span class="brand-dot"></span>TOLVENMARSK</div>
    <nav class="abs footer-nav"><span class="active" style="left:0">HOME</span><span style="left:30px">SHOP</span><span style="left:58px">QUALITY</span><span style="left:92px">ABOUT TOLVENMARSK</span><span style="left:146px">CONTACT US</span></nav>
    <div class="abs pay"><span>Payvia</span><span>Mercard</span><span>Vantia</span></div>
    <p class="abs center copy">Copyrights © 2020 Tolvenmarsk Honey. All Rights Reserved</p>
  </footer>
</div>

<!-- Home page, shop menu open -->
<div class="page page--menu">
  <header class="abs header">
    <div class="abs brand"><span class="brand-dot"></span>TOLVENMARSK</div>
    <div class="abs login">LOGIN</div>
    <div class="abs cart">&#128722; 0 / $0.00</div>
    <nav class="abs nav">
      <span class="active" style="left:0">HOME</span><span style="left:27px">SHOP ▾</span><span style="left:53px">QUALITY</span><span style="left:80px">ABOUT TOLVENMARSK</span><span style="left:134px">CONTACT US</span>
    </nav>
  </header>
  <section class="abs hero" role="img" aria-label="Honey pouring into a glass bowl among yellow flowers with bees"></section>
  <h1 class="abs hero-title">The Purest</h1>
  <p class="abs hero-sub">Teste of New Zealand</p>
  <div class="abs btn hero-btn">Shop Now</div>
  <div class="abs center dots hero-dots"><i></i><i class="on"></i><i></i></div>

  <div class="abs dropdown">
    <ul style="left:13px"><li>Sed ut perspiciatis</li><li>unde omnis iste natus</li><li>error sit voluptatem</li><li>accusantium</li><li>doloremque</li><li>laudantium</li><li>totam rem aperiam</li></ul>
    <ul style="left:81px"><li>Sed ut perspiciatis</li><li>unde omnis iste natus</li><li>error sit voluptatem</li><li>accusantium</li><li>doloremque</li><li>laudantium</li><li>totam rem aperiam</li></ul>
  </div>

  <h2 class="abs center title welcome-title">Welcome To Tolvenmarsk Honey</h2>
  <div class="abs center welcome-orn" style="top:270px"><div class="orn" role="img" aria-label="Gold ornamental flourish"></div></div>
  <p class="abs center para welcome-text" style="top:287px">Sed ut perspiciatis unde omnis iste natus error sit voluptatem accusantium doloremque laudantium, totam rem aperiam, eaque ipsa quae ab illo inventore veritatis et quasi architecto beatae vitae dicta sunt explicabo. Nemo enim ipsam volupt atem quia voluptas sit aspernatur aut odit aut fugit, sed quia consequuntur magni dolores eos qui ratione voluptatem ipsum quia dolor sit amet, consectetur, adipisci velit, sed quia non numquam eius</p>
  <div class="abs btn learn">LEARN MORE</div>

  <section class="abs products">
    <h2 class="abs center title">Our Products</h2>
    <div class="orn" role="img" aria-label="Gold ornamental flourish"></div>
    <p class="abs center sub">Sed ut perspiciatis unde omnis iste natus error sit voluptatem accusantium doloremque</p>
    <article class="abs card" style="left:33px"><div class="abs card-img" role="img" aria-label="Two jars of manuka honey MGO 100"></div><div class="abs center card-heart">♡</div><div class="abs center card-name">Miele Di Manuka MG100+</div><div class="abs center card-price">USD $18.00 – USD $22.00</div><div class="abs card-btn">BUY NOW</div></article>
    <article class="abs card" style="left:132px"><div class="abs card-img" role="img" aria-label="Jar of manuka honey MGO 300"></div><div class="abs center card-heart">♡</div><div class="abs center card-name">MGO 300+ Manuka Honey</div><div class="abs center card-price">USD $25.00 – USD $35.00</div><div class="abs card-btn">BUY NOW</div></article>
    <article class="abs card" style="left:231px"><div class="abs card-img" role="img" aria-label="Jar of manuka honey MGO 400"></div><div class="abs center card-heart">♡</div><div class="abs center card-name">MGO 400+ Manuka Honey</div><div class="abs center card-price">USD $25.00 – USD $35.00</div><div class="abs card-btn">BUY NOW</div></article>
    <div class="dots"><i></i><i class="on"></i><i></i></div>
  </section>

  <section class="abs video" role="img" aria-label="Beekeepers in protective suits tending hives in a field">
    <h2 class="abs center video-title">HOW OUR HONEY IS MADE</h2>
    <p class="abs center video-sub">Sed ut perspiciatis unde omnis iste natus error sit</p>
    <svg class="abs play" viewBox="0 0 30 30"><circle cx="15" cy="15" r="14" fill="rgba(0,0,0,.35)" stroke="#fff" stroke-width="1.2"/><path d="M12 9 L21 15 L12 21Z" fill="#fff"/></svg>
  </section>

  <section class="abs articles">
    <h2 class="abs center title">Latest Article</h2>
    <div class="orn" role="img" aria-label="Gold ornamental flourish"></div>
    <p class="abs center sub">Sed ut perspiciatis unde omnis iste natus error sit voluptatem accusantium doloremque</p>
    <article class="abs post" style="left:33px"><div class="abs post-img" role="img" aria-label="Bee on a pink flower" style="background:linear-gradient(135deg,#4d8a2e,#c24fb0 50%,#3e6b22)"></div><p class="abs center post-text">Sed ut perspiciatis unde omnis iste natus error</p><div class="abs post-meta">◉ 2 days ago</div></article>
    <article class="abs post" style="left:106px"><div class="abs post-img" role="img" aria-label="Beekeeper holding a honeycomb frame" style="background:linear-gradient(135deg,#d9cdb0,#b88a3a 50%,#6e4a1f)"></div><p class="abs center post-text">Sed ut perspiciatis unde omnis iste natus error</p><div class="abs post-meta">◉ 2 days ago</div></article>
    <article class="abs post" style="left:180px"><div class="abs post-img" role="img" aria-label="Bees on golden honeycomb" style="background:linear-gradient(135deg,#f0b426,#d98a10 50%,#8a5208)"></div><p class="abs center post-text">Sed ut perspiciatis unde omnis iste natus error</p><div class="abs post-meta">◉ 2 days ago</div></article>
    <article class="abs post" style="left:253px"><div class="abs post-img" role="img" aria-label="Honey in a glass bowl with yellow flowers" style="background:linear-gradient(135deg,#e8b830,#b5621a 50%,#6b3a12)"></div><p class="abs center post-text">Sed ut perspiciatis unde omnis iste natus error</p><div class="abs post-meta">◉ 2 days ago</div></article>
  </section>

  <section class="abs newsletter">
    <h2 class="abs center title">Our Newsletter</h2>
    <p class="abs center sub">Sed ut perspiciatis unde omnis iste natus error sit voluptatem accusantium doloremque</p>
    <div class="abs email">Email id :</div>
    <div class="abs submit">SUBMIT</div>
  </section>

  <footer class="abs footer">
    <div class="abs footer-brand"><span class="brand-dot"></span>TOLVENMARSK</div>
    <nav class="abs footer-nav"><span class="active" style="left:0">HOME</span><span style="left:30px">SHOP</span><span style="left:58px">QUALITY</span><span style="left:92px">ABOUT TOLVENMARSK</span><span style="left:146px">CONTACT US</span></nav>
    <div class="abs pay"><span>Payvia</span><span>Mercard</span><span>Vantia</span></div>
    <p class="abs center copy">Copyrights © 2020 Tolvenmarsk Honey. All Rights Reserved</p>
  </footer>
</div>

</body>
</html>
```